Home Remodeling company needs a business card design

we need a business card design for home remodeling company in hamilton county, indiana USA. we offers a wide range of construction services including whole house renovations, Design and Build Basements and Kitchen and Bathroom Remodeling . we would like to see designs for both site of business card that use the same color of the company logo and also including all information below :
1- Karim Feltous CEO / General Contractor
2- all company contacts Telephone numbers ( 1-888-DULOM-47 ) ( 317-555-0193) email address ( info@dulomhome.com) website ( www.dulomhome.com ) and social media logos (Facebook- twitter- google plus )
3- company logo
4- licensed . insured . bonded

```html
<!DOCTYPE html>
<html lang="en">
<head>
<meta charset="utf-8">
<title>Dulom Business Card</title>
<link rel="stylesheet" href="https://fonts.googleapis.com/css2?family=Open+Sans:wght@400;600;700&display=swap">
<style>
  :root {
    --stage: #e6e3df;
    --card-white: #ffffff;
    --card-dark: #333335;
    --ink: #1e1e1e;
    --ink-soft: #444446;
    --brand-red: #d0202a;
    --on-dark: #ffffff;
  }
  * { box-sizing: border-box; margin: 0; padding: 0; }
  html, body {
    width: 1200px; height: 844px; overflow: hidden;
    background: var(--stage);
    font-family: "Open Sans", Arial, sans-serif;
  }
  .stage {
    position: relative; width: 1200px; height: 844px;
    display: flex; align-items: center; justify-content: center; gap: 50px;
  }
  .card {
    position: relative; width: 525px; height: 300px;
    box-shadow: 0 6px 18px rgba(0,0,0,.18);
  }
  .card--front { background: var(--card-white); color: var(--ink); }
  .card--back { background: var(--card-dark); }

  .holder { position: absolute; left: 34px; top: 40px; }
  .holder__name { color: var(--brand-red); font-weight: 600; font-size: 17px; line-height: 1.2; }
  .holder__role { font-size: 13px; color: var(--ink); margin-top: 2px; }

  .brand { position: absolute; right: 40px; top: 52px; display: flex; flex-direction: column; align-items: flex-start; }
  .wordmark { display: flex; align-items: center; gap: 10px; }
  .wordmark__square { width: 14px; height: 14px; background: var(--brand-red); }
  .wordmark__name { font-weight: 700; font-size: 44px; letter-spacing: 1px; line-height: 1; color: var(--ink-soft); }
  .brand__credentials { margin-top: 10px; font-size: 13.5px; font-weight: 600; color: var(--ink); display: flex; align-items: center; gap: 6px; }
  .brand__dot { width: 6px; height: 6px; border-radius: 50%; background: var(--brand-red); }

  .contacts { position: absolute; left: 34px; top: 168px; list-style: none; }
  .contacts li { display: flex; align-items: center; gap: 8px; font-size: 13.5px; line-height: 21px; color: var(--ink); }
  .contacts svg { width: 12px; height: 12px; fill: var(--brand-red); flex: none; }

  .social { position: absolute; left: 34px; bottom: 22px; display: flex; gap: 7px; }
  .social__dot { width: 16px; height: 16px; border-radius: 50%; background: var(--ink); }

  .card--back .wordmark { position: absolute; left: 50%; top: 50%; transform: translate(-50%, -50%); }
  .card--back .wordmark__name { color: var(--on-dark); font-size: 56px; }
  .card--back .wordmark__square { width: 18px; height: 18px; }
</style>
</head>
<body>
<main class="stage">
  <section class="card card--front" aria-label="Business card front">
    <div class="holder">
      <p class="holder__name">Karim Feltous</p>
      <p class="holder__role">CEO / General Contractor</p>
    </div>

    <div class="brand">
      <div class="wordmark">
        <span class="wordmark__square"></span>
        <span class="wordmark__name">DULOM</span>
      </div>
      <p class="brand__credentials">Licensed <span class="brand__dot"></span> Insured <span class="brand__dot"></span> Bonded</p>
    </div>

    <ul class="contacts">
      <li><svg viewBox="0 0 24 24"><path d="M6.6 10.8a15 15 0 0 0 6.6 6.6l2.2-2.2a1 1 0 0 1 1-.25 11.4 11.4 0 0 0 3.6.57 1 1 0 0 1 1 1V20a1 1 0 0 1-1 1A17 17 0 0 1 3 4a1 1 0 0 1 1-1h3.5a1 1 0 0 1 1 1c0 1.25.2 2.45.57 3.6a1 1 0 0 1-.25 1z"/></svg>1-888-DULOM-47</li>
      <li><svg viewBox="0 0 24 24"><path d="M6.6 10.8a15 15 0 0 0 6.6 6.6l2.2-2.2a1 1 0 0 1 1-.25 11.4 11.4 0 0 0 3.6.57 1 1 0 0 1 1 1V20a1 1 0 0 1-1 1A17 17 0 0 1 3 4a1 1 0 0 1 1-1h3.5a1 1 0 0 1 1 1c0 1.25.2 2.45.57 3.6a1 1 0 0 1-.25 1z"/></svg>317-555-0193</li>
      <li><svg viewBox="0 0 24 24"><path d="M2 5h20v14H2zm2 2v.5l8 5 8-5V7l-8 5z"/></svg>info@dulomhome.com</li>
      <li><svg viewBox="0 0 24 24"><path d="M10 14a4 4 0 0 1 0-5.6l3-3a4 4 0 0 1 5.6 5.6l-1.5 1.5-1.4-1.4 1.5-1.5a2 2 0 0 0-2.8-2.8l-3 3a2 2 0 0 0 0 2.8zm4-4a4 4 0 0 1 0 5.6l-3 3a4 4 0 0 1-5.6-5.6l1.5-1.5 1.4 1.4-1.5 1.5a2 2 0 0 0 2.8 2.8l3-3a2 2 0 0 0 0-2.8z"/></svg>www.dulomhome.com</li>
    </ul>

    <div class="social" aria-label="Social media links">
      <span class="social__dot"></span>
      <span class="social__dot"></span>
      <span class="social__dot"></span>
    </div>
  </section>

  <section class="card card--back" aria-label="Business card back">
    <div class="wordmark">
      <span class="wordmark__square"></span>
      <span class="wordmark__name">DULOM</span>
    </div>
  </section>
</main>
</body>
</html>
```